Automotive Accessories Business Card

Design a business template that match our new logo design and our industry.

https://www.qelmotorgear.com/

Target Market(s)

Aftermarket auto parts and accessories

Industry/Entity Type

automotive

Contact Information for Business Card

company logo

Font styles to use
Serif
Sans Serif

Colors
EB3D1F
EC4F4E
F09395
F8D3D4
FCEDEE

```html
<!DOCTYPE html>
<html lang="en">
<head>
<meta charset="utf-8">
<title>QEL Motor Gear – Business Card</title>
<link href="https://fonts.googleapis.com/css2?family=Montserrat:wght@400;500;700;800&display=swap" rel="stylesheet">
<style>
  :root {
    --bg: #e9e9e9;
    --card: #434343;
    --red: #d8232a;
    --white: #ffffff;
    --emboss: #565656;
  }
  * { margin: 0; padding: 0; box-sizing: border-box; }
  html, body { width: 1200px; height: 802px; overflow: hidden; }
  body {
    background: var(--bg);
    font-family: "Montserrat", sans-serif;
    position: relative;
  }
  .card {
    position: absolute;
    top: 246px;
    width: 540px;
    height: 309px;
    background: var(--card);
    overflow: hidden;
  }
  .card--front { left: 40px; }
  .card--back { left: 620px; }

  /* front edges */
  .edge-bottom { position: absolute; left: 0; right: 0; bottom: 0; height: 10px; background: var(--red); }
  .edge-right-white { position: absolute; right: 0; top: 0; width: 14px; height: 150px; background: var(--white); }
  .edge-right-red { position: absolute; right: 0; top: 150px; bottom: 0; width: 14px; background: var(--red); }

  .brand {
    position: absolute; left: 34px; top: 62px;
    display: flex; align-items: center; gap: 9px;
  }
  .brand__mark { width: 14px; height: 14px; background: var(--red); flex: none; }
  .brand__name {
    color: var(--white); font-weight: 700; font-size: 21px;
    letter-spacing: 0.3px; text-transform: uppercase; white-space: nowrap;
  }

  .address {
    position: absolute; right: 38px; top: 34px;
    text-align: right; color: var(--white); font-size: 12.5px; line-height: 19px;
    font-style: normal;
  }

  .person { position: absolute; left: 34px; top: 150px; }
  .person__name {
    color: var(--red); font-weight: 800; font-size: 20px;
    letter-spacing: 2.5px; text-transform: uppercase;
  }
  .person__role { color: var(--white); font-size: 13px; margin-top: 2px; }

  .contact { position: absolute; left: 34px; top: 208px; list-style: none; }
  .contact li {
    display: flex; align-items: center; gap: 9px;
    color: var(--white); font-size: 12.5px; line-height: 20px;
  }
  .contact svg { width: 11px; height: 11px; flex: none; }
  .icon--fill { fill: var(--red); }
  .icon--line { fill: none; stroke: var(--red); stroke-width: 2.5; }

  /* back */
  .back-brand {
    position: absolute; inset: 0;
    display: flex; align-items: center; justify-content: center; gap: 14px;
  }
  .back-brand__mark { width: 22px; height: 22px; background: var(--emboss); }
  .back-brand__name {
    color: var(--emboss); font-weight: 700; font-size: 36px;
    letter-spacing: 1px; text-transform: uppercase; white-space: nowrap;
  }
  .card--back .edge-bottom { height: 4px; }
</style>
</head>
<body>
  <section class="card card--front">
    <div class="edge-bottom"></div>
    <div class="edge-right-white"></div>
    <div class="edge-right-red"></div>

    <div class="brand">
      <span class="brand__mark"></span>
      <span class="brand__name">QEL Motor Gear Inc</span>
    </div>

    <address class="address">
      240 W. Harbor Ave.<br>Suite B<br>Rivermont, CA 90210
    </address>

    <div class="person">
      <p class="person__name">Daniel Reyes</p>
      <p class="person__role">Manager</p>
    </div>

    <ul class="contact">
      <li>
        <svg class="icon--fill" viewBox="0 0 24 24" aria-hidden="true"><path d="M6.6 10.8a15.1 15.1 0 0 0 6.6 6.6l2.2-2.2c.3-.3.7-.4 1-.2 1.1.4 2.3.6 3.6.6.6 0 1 .4 1 1V20c0 .6-.4 1-1 1A17 17 0 0 1 3 4c0-.6.4-1 1-1h3.5c.6 0 1 .4 1 1 0 1.3.2 2.5.6 3.6.1.3 0 .7-.2 1z"/></svg>
        1-866-555-0148
      </li>
      <li>
        <svg class="icon--line" viewBox="0 0 24 24" aria-hidden="true"><rect x="2" y="5" width="20" height="14"/><path d="M2 5l10 8 10-8"/></svg>
        sales@qelmotorgear.com
      </li>
      <li>
        <svg class="icon--fill" viewBox="0 0 24 24" aria-hidden="true"><circle cx="12" cy="12" r="10"/></svg>
        www.qelmotorgear.com
      </li>
    </ul>
  </section>

  <section class="card card--back">
    <div class="back-brand">
      <span class="back-brand__mark"></span>
      <span class="back-brand__name">QEL Motor Gear Inc</span>
    </div>
    <div class="edge-bottom"></div>
  </section>
</body>
</html>
```